Harrowgate Care Assurance Ltd needs a business card and logo

We need a logo for documents, invoices etc and a business card to match. We are a health auditing, training and consulting company based in NZ and working in both Australia and NZ. We ensure health organisations meet all their compliance requirements and develop expertise in the health auditing sector. The design should in some way reflect either symbols for quality management in the health sector.

Target Market(s)

Health providers and those wishing to increase their capability in meeting and understanding compliance requirements

Industry/Entity Type

Business

Contact Information for Business Card

Logo plus contact details

Logo Text

Health auditing, consultancy and training

Requirements
Must have
• Name and contact details director: Marla Fenwick, mfenwick@hca-example.co.nz, PO Box 318, Warkworth, NZ, cell +6427391652

```html
<!DOCTYPE html>
<html lang="en">
<head>
<meta charset="utf-8">
<title>Harrowgate Care Assurance Ltd — Business Card</title>
<link rel="stylesheet" href="https://fonts.googleapis.com/css2?family=Source+Sans+3:wght@400;600&display=swap">
<style>
  :root {
    --backdrop: #3b3532;
    --card: #0d0d0d;
    --card-edge: #1a1a1a;
    --accent-blue: #1e9ae0;
    --accent-green: #5cb531;
    --text-light: #e6e6e6;
    --divider: #1b5f8c;
  }
  * { box-sizing: border-box; margin: 0; padding: 0; }
  html, body {
    width: 1200px;
    height: 900px;
    overflow: hidden;
    background: var(--backdrop);
    font-family: "Source Sans 3", "Myriad Pro", Arial, sans-serif;
  }
  .stage {
    position: relative;
    width: 1200px;
    height: 900px;
  }
  .card {
    position: absolute;
    top: 305px;
    width: 510px;
    height: 291px;
    background: var(--card);
    border: 1px solid var(--card-edge);
    box-shadow: 0 10px 24px rgba(0,0,0,0.45);
  }
  /* Front: contact side */
  .card--front { left: 60px; }
  .card--front .brand-mark {
    position: absolute;
    left: 38px;
    top: 78px;
    width: 150px;
    text-align: center;
  }
  .brand-mark__circle {
    display: block;
    margin: 0 auto 12px;
  }
  .brand-mark__name {
    color: var(--accent-green);
    font-weight: 600;
    font-size: 13px;
    line-height: 1.25;
  }
  .card--front .divider {
    position: absolute;
    left: 214px;
    top: 58px;
    width: 1px;
    height: 176px;
    background: linear-gradient(to bottom, transparent, var(--divider) 20%, var(--divider) 80%, transparent);
  }
  .contact {
    position: absolute;
    left: 236px;
    top: 66px;
    color: var(--text-light);
    font-size: 13px;
    line-height: 1.35;
  }
  .contact__name {
    color: var(--accent-blue);
    font-weight: 600;
    font-size: 16px;
  }
  .contact__role { margin-bottom: 22px; }
  .contact__address { margin-bottom: 6px; }
  .contact__line {
    display: flex;
    align-items: center;
    gap: 8px;
    margin-top: 3px;
  }
  .contact__line svg { flex: none; }

  /* Back: brand side */
  .card--back {
    left: 630px;
    display: flex;
    flex-direction: column;
    align-items: center;
    justify-content: center;
    gap: 14px;
  }
  .brand-lockup__name {
    color: var(--accent-green);
    font-weight: 600;
    font-size: 26px;
    letter-spacing: 0.5px;
    text-align: center;
    line-height: 1.15;
  }
</style>
</head>
<body>
<main class="stage">
  <section class="card card--front" aria-label="Business card, contact side">
    <div class="brand-mark">
      <svg class="brand-mark__circle" width="90" height="90" viewBox="0 0 90 90" aria-hidden="true">
        <circle cx="45" cy="45" r="40" fill="none" stroke="var(--accent-green)" stroke-width="6"/>
      </svg>
      <p class="brand-mark__name">Harrowgate Care<br>Assurance Ltd</p>
    </div>
    <div class="divider"></div>
    <div class="contact">
      <p class="contact__name">Marla Fenwick</p>
      <p class="contact__role">Director</p>
      <p class="contact__address">PO Box 318, Warkworth, NZ</p>
      <p class="contact__line">
        <svg width="10" height="14" viewBox="0 0 10 14" aria-hidden="true">
          <rect x="1" y="1" width="8" height="12" rx="1.5" fill="none" stroke="var(--accent-blue)" stroke-width="1.4"/>
          <circle cx="5" cy="10.5" r="0.9" fill="var(--accent-blue)"/>
        </svg>
        <span>+6427391652</span>
      </p>
      <p class="contact__line">
        <svg width="12" height="12" viewBox="0 0 24 24" aria-hidden="true">
          <path fill="var(--accent-blue)" d="M6.6 10.8a15.1 15.1 0 0 0 6.6 6.6l2.2-2.2a1 1 0 0 1 1-.25 11.4 11.4 0 0 0 3.6.57 1 1 0 0 1 1 1V20a1 1 0 0 1-1 1A17 17 0 0 1 3 4a1 1 0 0 1 1-1h3.5a1 1 0 0 1 1 1c0 1.25.2 2.45.57 3.57a1 1 0 0 1-.25 1z"/>
        </svg>
        <span>mfenwick@hca-example.co.nz</span>
      </p>
    </div>
  </section>

  <section class="card card--back" aria-label="Business card, brand side">
    <svg width="56" height="56" viewBox="0 0 56 56" aria-hidden="true">
      <circle cx="28" cy="28" r="24" fill="none" stroke="var(--accent-green)" stroke-width="4"/>
    </svg>
    <p class="brand-lockup__name">Harrowgate Care<br>Assurance Ltd</p>
  </section>
</main>
</body>
</html>
```